Brightwave Charters website

Looking to have a new, interactive website built on Wordpress and hosted by hostorra. Our current site was made and is hosted by plim and has been up and running for 8 years. Would like to replace as seamlessly as possible. Attached are general ideas for the site as well as requirements. Would like to showcase our charter options and information on the home page with Our Charters, FAQ and Gallery as follow up pages. Would like to be created in Wordpress and HTTPS

Target Market(s)

Vacationing tourists visiting Siesta Key

Industry/Entity Type

Boat Charters

Number of Pages Required

1 page

Requirements
Must have
• Website must be secure, HTTPS not HTTP . . Use webp images throughout the entire site. Info for the home page was uploaded on 3 seperate pages labeled home1, home2 and home3. Need the bottom, above footer, to show What Our Customers Say About Us with reviews from Plentora, Zentrix and QM. Homepage to have all 6 charter options and info provided on the attached docx labeled home1, home2 and home3 . If we can get the 3 pages following the home page (Our Charters,FAQ and Gallery) I had also attached brief summaries for those pages. Install these Plug-ins, MERV, Slotwise (free), Blockforge plugin. Any other plugin needs to be approved by us

```html
<!DOCTYPE html>
<html lang="en">
<head>
<meta charset="utf-8">
<title>Brightwave Charters</title>
<link href="https://fonts.googleapis.com/css2?family=Poppins:wght@300;400;500;600;700;800&display=swap" rel="stylesheet">
<style>
:root{
  --navy:#1c2a86;
  --royal:#1f3f9e;
  --heading:#1d3a94;
  --sky:#c9e7f8;
  --card:#dcf0fb;
  --orange:#f07a1a;
  --orange-light:#f59a3a;
  --text:#2b2b2b;
  --white:#ffffff;
  --red:#e23b2a;
}
*{box-sizing:border-box;margin:0;padding:0}
html,body{width:1200px;height:3942px;overflow:hidden}
body{font-family:'Poppins',sans-serif;color:var(--text);background:var(--white);position:relative}
.abs{position:absolute}
.btn{position:absolute;display:flex;align-items:center;justify-content:center;border-radius:30px;background:linear-gradient(180deg,var(--orange-light),var(--orange));color:#fff;font-weight:700;font-size:15px;letter-spacing:.5px;text-transform:uppercase}

/* header */
.header{position:absolute;left:0;top:0;width:1200px;height:132px;background:#fff;z-index:5}
.logo-badge{position:absolute;left:78px;top:20px;width:158px;height:158px;border-radius:50%;background:#fff;display:flex;align-items:center;justify-content:center;text-align:center;z-index:6}
.logo-badge span{font-weight:800;font-size:21px;line-height:1.1;color:var(--royal)}
.call{position:absolute;left:732px;top:18px;display:flex;align-items:center;gap:8px}
.icon-circle{width:38px;height:38px;border-radius:50%;background:#1f63c6;display:flex;align-items:center;justify-content:center}
.call small{display:block;color:var(--red);font-weight:600;font-size:13px;line-height:1}
.call strong{display:block;color:var(--heading);font-weight:700;font-size:24px;line-height:1.2}
.top-book{left:986px;top:26px;width:141px;height:37px;font-size:16px;text-transform:none}
.nav{position:absolute;left:592px;top:81px;width:608px;height:51px;background:var(--royal);clip-path:polygon(30px 0,100% 0,100% 100%,0 100%)}
.nav ul{list-style:none;display:flex;position:absolute;left:44px;top:0;height:51px;align-items:center;gap:40px}
.nav li{color:#fff;font-weight:600;font-size:14px}
.nav li.active{color:var(--orange-light);border-bottom:2px solid var(--orange-light)}

/* hero */
.hero{position:absolute;left:0;top:132px;width:1200px;height:672px;overflow:hidden}
.hero-photo{position:absolute;inset:0;background:linear-gradient(180deg,#8fb4d8 0%,#7a98b7 30%,#8c8a80 55%,#7b7468 80%,#5d5a54 100%)}
.hero-photo::after{content:"";position:absolute;inset:0;background:radial-gradient(ellipse at 55% 55%,rgba(40,70,140,.35),transparent 60%)}
.hero-text{position:absolute;left:0;width:1200px;text-align:center;color:#fff;text-shadow:0 2px 8px rgba(0,0,0,.35)}
.hero .welcome{top:262px;font-weight:300;font-size:50px;line-height:1}
.hero .name{top:308px;font-weight:800;font-size:66px;line-height:1}
.hero .tag{top:391px;font-weight:800;font-size:40px;line-height:1}
.hero-book{left:510px;top:469px;width:179px;height:46px}
.dots{position:absolute;left:562px;top:570px;display:flex;gap:11px}
.dots i{width:10px;height:10px;border-radius:50%;background:#fff}
.dots i.on{background:var(--orange)}

/* charters */
.section-title{position:absolute;left:0;width:1200px;text-align:center;font-size:46px;font-weight:300;color:#1a1a1a;line-height:1}
.section-title b{font-weight:800;color:var(--heading)}
.charter{position:absolute;width:329px;height:242px;background:var(--card);border-radius:12px;overflow:hidden}
.charter.active{border:3px solid #1f6fd0}
.charter .photo{height:174px}
.charter h3{height:68px;display:flex;align-items:center;justify-content:center;color:var(--heading);font-weight:700;font-size:20px}

/* book band */
.band{position:absolute;left:0;width:1200px}
.book-heading{position:absolute;left:75px;top:1752px;font-size:48px;line-height:1.03;font-weight:300;color:#fff}
.book-heading b{font-weight:800}
.book-copy{position:absolute;left:75px;top:1920px;width:620px;font-size:14.5px;line-height:28px;color:#fff}
.round-photo{position:absolute;border-radius:50%}

/* about */
.about-heading{position:absolute;left:525px;top:2352px;font-size:48px;line-height:1;font-weight:300;color:#1a1a1a}
.about-heading b{display:block;font-weight:800;color:var(--heading)}
.about-copy{position:absolute;left:525px;top:2462px;width:620px;font-size:14.5px;line-height:26.5px;color:#333}

/* reviews */
.reviews-title{position:absolute;left:0;top:3050px;width:1200px;text-align:center;color:#fff;font-size:46px;line-height:50px;font-weight:300}
.reviews-title b{font-weight:800}
.review{position:absolute;top:3173px;width:329px;height:268px;background:#fff;border-radius:10px;overflow:hidden}
.review-head{height:58px;border-bottom:1px solid #ddd;display:flex;align-items:center;gap:10px;padding-left:14px;font-weight:600;font-size:21px;color:#1a1a1a}
.mark{width:26px;height:26px;border-radius:50%;background:#3b3b3b;flex:none}
.review-body{padding:18px 18px 0 18px;font-size:13px;line-height:21.5px;color:#333}
.stars{color:#f39a1e;font-size:19px;letter-spacing:3px;line-height:1}
.stars.green{color:#22b35a}
.reviewer{display:flex;align-items:center;gap:10px;margin-bottom:14px}
.avatar{width:48px;height:48px;border-radius:50%;background:#e5e5e5;display:flex;align-items:center;justify-content:center;color:#555;font-weight:600;font-size:20px;flex:none}
.reviewer .nm{font-weight:600;font-size:17px;color:#1a1a1a;line-height:1.2}
.reviewer .nm.blue{color:#2c56b8}
.reviewer .ago{font-size:13px;font-style:italic;color:#888}
.review-title{font-weight:600;font-size:17px;color:#1a1a1a;margin:6px 0 8px}

/* footer */
.footer-logo{position:absolute;left:75px;top:3712px;width:140px;height:130px;display:flex;align-items:center;justify-content:center;text-align:center}
.footer-logo span{font-weight:800;font-size:20px;line-height:1.1;color:var(--royal)}
.copyright{position:absolute;left:77px;top:3860px;font-size:11.5px;line-height:19px;color:#333}
.contact{position:absolute;top:3712px;display:flex;gap:14px}
.contact .icon-circle{width:52px;height:52px;background:#1f5fc4}
.contact h4{color:#1f6fd0;font-weight:600;font-size:19px;line-height:1.3}
.contact p{font-size:16px;line-height:24px;color:#333}
.footer-rule{position:absolute;left:343px;top:3806px;width:784px;height:1px;background:#ddd}
.footer-nav{position:absolute;top:3828px;right:73px;display:flex;gap:48px;font-size:16px;font-weight:500;color:#222}
.social{position:absolute;top:3880px;right:73px;display:flex;gap:20px}
.social i{width:20px;height:20px;border-radius:50%;background:#333;display:block}
</style>
</head>
<body>

<header class="header">
  <div class="logo-badge" role="img" aria-label="Brightwave Charters"><span>Brightwave<br>Charters</span></div>
  <div class="call">
    <div class="icon-circle"><svg width="20" height="20" viewBox="0 0 24 24"><path fill="#fff" d="M6.6 10.8c1.4 2.8 3.8 5.1 6.6 6.6l2.2-2.2c.3-.3.7-.4 1-.2 1.1.4 2.3.6 3.6.6.6 0 1 .4 1 1V20c0 .6-.4 1-1 1C10.6 21 3 13.4 3 4c0-.6.4-1 1-1h3.5c.6 0 1 .4 1 1 0 1.3.2 2.5.6 3.6.1.3 0 .7-.2 1z"/></svg></div>
    <div><small>Call Us Today:</small><strong>941/555-0182</strong></div>
  </div>
  <div class="btn top-book">Book Now</div>
  <nav class="nav"><ul>
    <li class="active">HOME</li><li>OUR CHARTERS</li><li>FAQ</li><li>GALLERY</li><li>CONTACT</li>
  </ul></nav>
</header>

<section class="hero">
  <div class="hero-photo" role="img" aria-label="Family standing on a dock in front of a charter boat on Siesta Key"></div>
  <div class="hero-text welcome">WELCOME TO</div>
  <div class="hero-text name">BRIGHTWAVE CHARTERS</div>
  <div class="hero-text tag">BEST PRIVATE BOAT TOUR ON SIESTA</div>
  <div class="btn hero-book">Book Now</div>
  <div class="dots"><i></i><i class="on"></i><i></i><i></i></div>
  <svg class="abs" style="left:0;bottom:0" width="1200" height="90" viewBox="0 0 1200 90" preserveAspectRatio="none"><path fill="#fff" d="M0 20 C 200 90, 420 90, 620 60 S 1000 10, 1200 30 L1200 90 L0 90 Z"/></svg>
</section>

<h2 class="section-title" style="top:864px">OUR <b>CHARTER</b></h2>

<div class="charter" style="left:75px;top:940px"><div class="photo" role="img" aria-label="Dolphin leaping beside a boat wake" style="background:linear-gradient(180deg,#6aa6e0,#2f6aa8 55%,#c9d7e3)"></div><h3>DOLPHIN/WILDLIFE TOURS</h3></div>
<div class="charter active" style="left:436px;top:940px"><div class="photo" role="img" aria-label="Sandcastle and shells on a sandbar beach" style="background:linear-gradient(180deg,#8cc6ef,#bfe3f2 45%,#e6d3b3)"></div><h3>SANDBAR FUN</h3></div>
<div class="charter" style="left:797px;top:940px"><div class="photo" role="img" aria-label="Snorkeler swimming over a coral reef" style="background:linear-gradient(180deg,#5aa0dc,#2a88c5 45%,#1f6b95)"></div><h3>SNORKELING</h3></div>
<div class="charter" style="left:75px;top:1211px"><div class="photo" role="img" aria-label="Shallow clear water along a white sand beach" style="background:linear-gradient(180deg,#3c7fd0,#8ec5e0 40%,#cfe0c8 70%,#e6e2cf)"></div><h3>SHELLING &amp; BEACHES</h3></div>
<div class="charter" style="left:436px;top:1211px"><div class="photo" role="img" aria-label="Guests at an outdoor waterfront tiki bar" style="background:linear-gradient(180deg,#9bb5a0,#7b7a6a 50%,#c99a7c)"></div><h3>TIKI BAR CRAWL</h3></div>
<div class="charter" style="left:797px;top:1211px"><div class="photo" role="img" aria-label="Red sun setting over the water behind a boat" style="background:linear-gradient(180deg,#b9646a,#9a6b70 45%,#6b5a5c)"></div><h3>SUNSET CRUISE</h3></div>

<svg class="band" style="top:1515px" width="1200" height="765" viewBox="0 0 1200 765" preserveAspectRatio="none">
  <path fill="#c9e7f8" d="M0 110 C 250 180, 420 120, 620 50 S 1000 -10, 1200 60 L1200 700 C 980 640, 780 720, 560 750 S 150 700, 0 600 Z"/>
  <path fill="#1c2a86" d="M0 135 C 250 200, 430 150, 640 80 S 1000 30, 1200 90 L1200 665 C 980 610, 780 700, 560 725 S 150 680, 0 585 Z"/>
</svg>
<div class="abs" role="img" aria-label="Sailboat on dark evening water" style="left:0;top:1620px;width:1200px;height:560px;background:radial-gradient(ellipse at 60% 40%,rgba(70,90,170,.35),transparent 65%)"></div>
<h2 class="book-heading">BOOK YOUR SIESTA<br>KEY <b>BOAT CHARTER<br>TODAY!</b></h2>
<p class="book-copy">Dolphin Tours, Snorkeling, Sandbars, Tiki Bars, Shelling, Sunsets.<br>Design your day on the water. Customize your day your way! Call or Email to<br>coordinate and get help with suggestions</p>
<div class="btn" style="left:75px;top:2027px;width:181px;height:49px">Book Now</div>
<div class="round-photo" style="left:700px;top:1655px;width:430px;height:430px;background:#0f1a55"></div>
<div class="round-photo" role="img" aria-label="Group of friends seated on a boat deck on the water" style="left:704px;top:1659px;width:422px;height:422px;background:linear-gradient(180deg,#6aa3c7,#4fa9b4 40%,#c9b9a3 70%,#8a7a6a)"></div>

<div class="round-photo" style="left:79px;top:2364px;width:426px;height:426px;background:#c8c8c8"></div>
<div class="round-photo" role="img" aria-label="Speedboat cruising past waterfront buildings" style="left:75px;top:2358px;width:424px;height:424px;background:linear-gradient(180deg,#7fb1de,#a9c2d6 35%,#3f6f9c 55%,#2a5580)"></div>
<h2 class="about-heading">ABOUT<b>BRIGHTWAVE CHARTERS</b></h2>
<div class="about-copy">
  <p>Welcome to the BEST private charter on and around Siesta Key! Whether you<br>live on Siesta Key, Sarasota or are one of our many welcome visitors... we want<br>you to enjoy the day on the crystal clear waters and pristine beaches.</p>
  <p>My name is Dan Corliss and I look forward to being your Captain for the day.</p>
  <p>My goal is to ensure a safe and fun time on the water. &nbsp;I will work hard to create<br>unforgettable memories with a charter that you, your family and friends will<br>remember. &nbsp;I have been boating since the age of 13 and am a USCG licensed<br>Master Captain. We will take your private party of up to 6 people, out from<br>2 hours up to a full 8 hour day charter.</p>
</div>
<div class="btn" style="left:525px;top:2732px;width:179px;height:49px;font-size:14px">Read More</div>

<svg class="band" style="top:2847px" width="1200" height="803" viewBox="0 0 1200 803" preserveAspectRatio="none">
  <path fill="#c9e7f8" d="M0 100 C 220 150, 420 110, 640 40 S 1020 0, 1200 40 L1200 690 C 1000 620, 760 740, 520 790 S 150 740, 0 690 Z"/>
  <path fill="#1c2a86" d="M0 125 C 220 175, 430 140, 660 70 S 1020 30, 1200 70 L1200 670 C 1000 600, 760 720, 520 765 S 150 720, 0 670 Z"/>
</svg>
<div class="abs" role="img" aria-label="Boat silhouette against dark water" style="left:600px;top:2880px;width:520px;height:720px;background:radial-gradient(ellipse at 40% 50%,rgba(20,25,70,.55),transparent 65%)"></div>
<h2 class="reviews-title">WHAT OUR CHARTER <b>GUESTS HAVE<br>TO SAY ABOUT US</b></h2>

<div class="review" style="left:75px">
  <div class="review-head"><span class="mark"></span>Plentora Reviews</div>
  <div class="review-body">
    <div class="stars green">★★★★★</div>
    <div class="review-title">Down time and Dolphins</div>
    Dan took my husband and I out for an afternoon to decompress from hurricane cleanup and evacuation.. His boat was immaculate and very comfortable for an afternoon cruise to Venice .
  </div>
</div>
<div class="review" style="left:436px">
  <div class="review-head"><span class="mark"></span>Zentrix Reviews</div>
  <div class="review-body">
    <div class="reviewer"><div class="avatar">R</div><div><div class="nm">Name Heading</div><div class="stars">★★★★★</div></div></div>
    Dan took my husband and I out for an afternoon to decompress from hurricane cleanup and evacuation.. His boat was immaculate and very comfortable for an afternoon cruise to Venice .
  </div>
</div>
<div class="review" style="left:797px">
  <div class="review-head"><span class="mark"></span>QM Reviews</div>
  <div class="review-body">
    <div class="reviewer"><div class="avatar"><svg width="22" height="22" viewBox="0 0 24 24"><circle cx="12" cy="8" r="5" fill="#555"/><path d="M3 22c0-5 4-8 9-8s9 3 9 8z" fill="#555"/></svg></div><div><div class="nm blue">Name Heading</div><div class="ago">2 days ago</div></div></div>
    Dan took my husband and I out for an afternoon to decompress from hurricane cleanup and evacuation.. His boat was immaculate and very comfortable for an afternoon cruise to Venice .
  </div>
</div>

<footer>
  <div class="footer-logo" role="img" aria-label="Brightwave Charters"><span>Brightwave<br>Charters</span></div>
  <div class="copyright">© Copyright 2024 Brightwave Charters<br>All Rights Reserved.</div>
  <div class="contact" style="left:343px">
    <div class="icon-circle"><svg width="22" height="22" viewBox="0 0 24 24"><path fill="#fff" d="M12 2a7 7 0 0 0-7 7c0 5 7 13 7 13s7-8 7-13a7 7 0 0 0-7-7zm0 9.5A2.5 2.5 0 1 1 12 6.5a2.5 2.5 0 0 1 0 5z"/></svg></div>
    <div><h4>Address</h4><p>4120 Harbor Tide Rd,<br>Siesta Key</p></div>
  </div>
  <div class="contact" style="left:615px">
    <div class="icon-circle"><svg width="22" height="22" viewBox="0 0 24 24"><path fill="#fff" d="M6.6 10.8c1.4 2.8 3.8 5.1 6.6 6.6l2.2-2.2c.3-.3.7-.4 1-.2 1.1.4 2.3.6 3.6.6.6 0 1 .4 1 1V20c0 .6-.4 1-1 1C10.6 21 3 13.4 3 4c0-.6.4-1 1-1h3.5c.6 0 1 .4 1 1 0 1.3.2 2.5.6 3.6.1.3 0 .7-.2 1z"/></svg></div>
    <div><h4>Phone</h4><p style="font-size:18px">941-555-0182</p></div>
  </div>
  <div class="contact" style="left:875px">
    <div class="icon-circle"><svg width="22" height="22" viewBox="0 0 24 24"><path fill="#fff" d="M3 5h18v14H3z"/><path d="M3 6l9 7 9-7" stroke="#1f5fc4" stroke-width="2" fill="none"/></svg></div>
    <div><h4>Email</h4><p style="font-size:14px">hello@brightwavecharters.com</p></div>
  </div>
  <div class="footer-rule"></div>
  <nav class="footer-nav"><span>Home</span><span>Our Charters</span><span>FAQ</span><span>Gallery</span><span>Contact</span></nav>
  <div class="social" aria-label="Social links"><i></i><i></i><i></i><i></i><i></i></div>
</footer>

</body>
</html>
```